Build a landing page to promote a service (dialler consultation and support).

We are a call centre consultation firm and we need a landing page to promote a service. The service is Tormalux dialler consultation and support.
If you do not know what Tormalux is, please do some quick "Zorvex" research for more information.
The landing page will be promoted with a paid advertisement, so we want something that is simple, and explains exactly what service we offer.
There are two objectives for the landing page:
1) A "call to action" which directs the user to a contact page, including a form plus all of our contact details.
2) A form for them viewers to enter their details to get a "FREE" quote for their project. This form should be placed on the main page.
Notes:
The call to action will require the viewer to enter their name, email, phone number as well as a description of their request. There will also need to be a drop down menu for the type of quote. This menu should have the following options:
1) Tormalux support
2) Tormalux hosting
3) Tormalux customisation
4) Other
We need 2 pages in total:
1) Main landing page
This is the home page. It will need to clearly indicate our services and our key selling features.
Services:
* Tormalux support
* Tormalux hosting
* Tormalux customisation
Key Selling Features:
* Australian based
* PCI complaint
* 10+ years of dialler and call centre experience
* we run a sister company which is a highly reputable 40 seat call centre, so we know first hand about call centre technology.
The main landing page will have an "about us" section with a few paragraphs about how we got started.
-------------------------------------------------------------------------
2) Contact page
All of our contact details will live on this page, as well as a contact form.
Other notes:
We will be self hosting the landing page.
We already have a domain name.
The design must be clean and incorporate our logo, as well as it's colours. (Logo attached)
We want a fully function HTML landing page, not just a "PSD" design.
The page must be mobile optimised.
Anyone using Tormalux software.

```html
<!DOCTYPE html>
<html lang="en">
<head>
<meta charset="utf-8">
<title>Contact Us – Ravenmoor</title>
<link href="https://fonts.googleapis.com/css2?family=Catamaran:wght@600;700&family=Poppins:wght@400;500;600&display=swap" rel="stylesheet">
<style>
  :root {
    --brand: #1a8cd4;
    --brand-bright: #2aa8ec;
    --ink: #222;
    --muted: #555;
    --line: #c9c9c9;
    --footer: #121212;
    --footer-bar: #1a90d6;
    --white: #fff;
  }
  * { box-sizing: border-box; margin: 0; padding: 0; }
  html, body { width: 1200px; height: 2161px; overflow: hidden; }
  body { position: relative; background: var(--white); font-family: "Poppins", sans-serif; color: var(--ink); }
  .abs { position: absolute; }

  /* Header */
  .site-header { position: absolute; left: 0; top: 0; width: 1200px; height: 146px; border-bottom: 4px solid #eee; }
  .brand { position: absolute; left: 88px; top: 40px; display: flex; align-items: center; gap: 12px; }
  .brand-dot { width: 48px; height: 48px; border-radius: 50%; background: var(--brand); }
  .brand-name { font-family: "Poppins", sans-serif; font-weight: 500; font-size: 38px; color: var(--brand); }
  .main-nav { position: absolute; top: 60px; left: 510px; display: flex; gap: 46px; font-size: 17px; color: #555; }
  .main-nav .current { color: var(--brand); font-weight: 600; }
  .search-icon { position: absolute; left: 1076px; top: 63px; }

  /* Hero */
  .hero { position: absolute; left: 0; top: 150px; width: 1200px; height: 356px;
    background: linear-gradient(100deg, #4a4f57 0%, #707a86 45%, #b3a89a 75%, #8d8a86 100%); }
  .hero-title { position: absolute; left: 80px; top: 130px; font-family: "Catamaran", sans-serif; font-weight: 700; font-size: 40px; color: var(--white); }
  .breadcrumb { position: absolute; left: 82px; top: 200px; font-size: 16px; color: var(--white); font-weight: 500; }

  .section-title { position: absolute; left: 0; width: 1200px; text-align: center; font-family: "Catamaran", sans-serif; font-weight: 700; font-size: 42px; color: var(--brand); }
  .title-rule { position: absolute; left: 565px; width: 72px; height: 4px; background: var(--brand); }
  .intro { position: absolute; left: 0; top: 645px; width: 1200px; text-align: center; font-size: 18px; line-height: 32px; color: var(--muted); }

  .map { position: absolute; left: 80px; top: 753px; width: 717px; height: 356px;
    background: linear-gradient(135deg, #ece8d8 0%, #dfe5cf 40%, #eee9dc 70%, #e6e3d6 100%); }
  .info { position: absolute; left: 836px; width: 320px; }
  .info h3 { font-family: "Catamaran", sans-serif; font-weight: 700; font-size: 27px; color: var(--brand); }
  .info p { font-size: 19px; line-height: 36px; color: #111; font-weight: 500; }

  /* Contact block */
  .follow-panel { position: absolute; left: 537px; top: 1271px; width: 583px; height: 474px;
    background: linear-gradient(160deg, #39b2ef 0%, #23a1e6 60%, #1d96dd 100%); }
  .follow-panel h2 { position: absolute; left: 0; top: 110px; width: 100%; padding-left: 110px; text-align: center; font-family: "Catamaran", sans-serif; font-weight: 700; font-size: 42px; color: var(--white); }
  .follow-panel p { position: absolute; left: 100px; top: 186px; width: 386px; padding-left: 0; text-align: center; font-size: 19px; line-height: 36px; color: var(--white); margin-left: 50px; }
  .socials { position: absolute; left: 177px; top: 305px; display: flex; gap: 22px; }
  .socials span { width: 28px; height: 28px; border-radius: 50%; background: var(--white); }

  .form-card { position: absolute; left: 66px; top: 1306px; width: 535px; height: 405px; background: var(--white); box-shadow: 0 2px 14px rgba(0,0,0,.08); }
  .form-card h3 { position: absolute; left: 41px; top: 28px; font-family: "Catamaran", sans-serif; font-weight: 700; font-size: 33px; color: var(--brand); }
  .field { position: absolute; height: 44px; border: 1px solid var(--line); font-size: 14px; color: #888; padding: 12px 17px; }
  .submit { position: absolute; left: 41px; top: 331px; width: 132px; height: 43px; background: var(--brand); color: var(--white); font-weight: 600; font-size: 17px; display: flex; align-items: center; justify-content: center; }

  /* Footer */
  .site-footer { position: absolute; left: 0; top: 1817px; width: 1200px; height: 282px; background: var(--footer); color: var(--white); }
  .site-footer h4 { position: absolute; top: 42px; font-size: 19px; font-weight: 600; }
  .f-list { position: absolute; list-style: none; font-size: 14.5px; }
  .f-contact { position: absolute; left: 83px; font-size: 14.5px; line-height: 22px; display: flex; gap: 16px; }
  .f-contact svg { flex: none; margin-top: 2px; }
  .newsletter-text { position: absolute; left: 871px; top: 86px; width: 250px; font-size: 14.5px; line-height: 26px; }
  .newsletter-input { position: absolute; left: 871px; top: 185px; width: 204px; height: 44px; background: var(--white); color: #777; font-size: 13px; padding: 13px 12px; }
  .newsletter-btn { position: absolute; left: 1075px; top: 185px; width: 44px; height: 44px; background: var(--brand); display: flex; align-items: center; justify-content: center; }
  .copyright { position: absolute; left: 0; top: 2099px; width: 1200px; height: 62px; background: var(--footer-bar); color: var(--white); text-align: center; line-height: 62px; font-size: 15.5px; }
</style>
</head>
<body>
  <header class="site-header">
    <div class="brand"><span class="brand-dot"></span><span class="brand-name">Ravenmoor</span></div>
    <nav class="main-nav">
      <span>Home</span><span>About Us</span><span>Services</span><span>Features</span><span class="current">Contact Us</span>
    </nav>
    <svg class="search-icon" width="16" height="16" viewBox="0 0 16 16"><circle cx="6.5" cy="6.5" r="4.5" fill="none" stroke="#444" stroke-width="2"/><line x1="10" y1="10" x2="14" y2="14" stroke="#444" stroke-width="2.4"/></svg>
  </header>

  <section class="hero" role="img" aria-label="Photo of smiling call centre agents wearing headsets">
    <h1 class="hero-title">Contact us</h1>
    <div class="breadcrumb">Home &nbsp;/&nbsp; Contact Us</div>
  </section>

  <h2 class="section-title" style="top:556px">Get in touch with us</h2>
  <div class="title-rule" style="top:626px"></div>
  <p class="intro">Lorem ipsum dolor sit amet, consectetur adipiscing elit, sed do eiusmod<br>tempor incididunt ut labore et dolore magna aliqua.</p>

  <div class="map" role="img" aria-label="Map of the western United States with an office location marker"></div>

  <div class="info" style="top:780px"><h3>Address</h3><p>No.72, Brindle Lane, Harwick,<br>FL 2049</p></div>
  <div class="info" style="top:912px"><h3>Phone</h3><p>+1-555-014-2260</p></div>
  <div class="info" style="top:998px"><h3>Email</h3><p>hello@ravenmoor.net</p></div>

  <h2 class="section-title" style="top:1162px">Contact Us</h2>
  <div class="title-rule" style="top:1231px"></div>

  <section class="follow-panel" role="img" aria-label="Blue tinted photo of support agents at their desks">
    <h2 style="padding-left:0">Follow Us</h2>
    <p style="left:57px;margin-left:0;width:470px">Lorem ipsum dolor sit amet, consectetur adipiscing elit sed do</p>
    <div class="socials" style="left:178px"><span></span><span></span><span></span><span></span><span></span></div>
  </section>

  <form class="form-card">
    <h3>Get In Touch</h3>
    <div class="field" style="left:43px;top:91px;width:217px">Name</div>
    <div class="field" style="left:280px;top:91px;width:216px">Email</div>
    <div class="field" style="left:43px;top:155px;width:217px">Phone Number</div>
    <div class="field" style="left:280px;top:155px;width:216px">Subject</div>
    <div class="field" style="left:43px;top:220px;width:453px;height:86px">Message</div>
    <div class="submit">Submit</div>
  </form>

  <footer class="site-footer">
    <h4 style="left:83px">Contact Us</h4>
    <div class="f-contact" style="top:88px">
      <svg width="14" height="18" viewBox="0 0 14 18"><path d="M7 0a7 7 0 0 0-7 7c0 5 7 11 7 11s7-6 7-11a7 7 0 0 0-7-7z" fill="#fff"/><circle cx="7" cy="7" r="2.5" fill="#121212"/></svg>
      <span>No.72, Brindle Lane,<br>Harwick, FL 2049</span>
    </div>
    <div class="f-contact" style="top:155px">
      <svg width="16" height="16" viewBox="0 0 16 16"><path d="M3 1l3 3-2 2c1 2 3 4 6 6l2-2 3 3-2 3C7 15 1 9 0 4z" fill="#fff"/></svg>
      <span>+1-555-014-2260</span>
    </div>
    <div class="f-contact" style="top:195px">
      <svg width="18" height="14" viewBox="0 0 18 14"><rect width="18" height="14" fill="#fff"/><path d="M0 0l9 7 9-7" fill="none" stroke="#121212" stroke-width="1.5"/></svg>
      <span>hello@ravenmoor.net</span>
    </div>

    <h4 style="left:415px">Links</h4>
    <ul class="f-list" style="left:415px;top:90px;line-height:32px">
      <li>Home</li><li>About Us</li><li>Services</li><li>Features</li><li>Contact Us</li>
    </ul>

    <h4 style="left:600px">Services</h4>
    <ul class="f-list" style="left:600px;top:90px;line-height:34px">
      <li>Tormalux Support</li><li>Tormalux hosting</li><li>Tormalux Customisation</li>
    </ul>

    <h4 style="left:871px">Newsletter</h4>
    <p class="newsletter-text">But I must explain to you how all this mistaken idea of enouncing pleasure and praising.</p>
    <div class="newsletter-input">Enter your email address</div>
    <div class="newsletter-btn"><svg width="14" height="12" viewBox="0 0 14 12"><path d="M0 6h12M7 1l5 5-5 5" fill="none" stroke="#fff" stroke-width="2"/></svg></div>
  </footer>

  <div class="copyright">© 2018 Copyrights | All Rights Reserved</div>
</body>
</html>
```